Simple, 1-Page Project - Life-saving AED Devices

We recently kicked off a project to bring all geographic location records for automatic emergency defibrillators (AEDs) in the State of New York online (instead of kept in paper in drawers). This hope is that is will ultimately save thousands of lives, as 9-1-1 operators will be able to quickly direct civilians to the nearest AED to bring to people suffering a cardiac event (e.g., a heart attack).

This page will be used to describe this effort, our progress thus far and how far we have left to go.

I am looking for a 1-page design - coded for both a responsive version for mobile devices and a traditional version - that would ***ideally*** plug into my existing WordPress site (https://qv-lmt.org), but it's not a requirement.

Target Market(s)

General public (non-physicians/non-EMTs)

Requirements
Must have
• - Our logo (please note, our logo is the Birchfield Vale Chapter logo...attached)
Nice to have
• - Would be wonderful to have an area with a clickable map showing where the participating regions are - which, once clicked, will take to you their specific sites. Regions are large chunks of land encompassing multiple towns, NOT a singular, specific place A nice-looking Google Map, a la Plumtail Grids (https://plumtailgrids.com/) would be cool if this were possible..
• - If you need a headline or page title, you can use: "Bringing AEDs in New York Online"
• - Would be nice if the design incorporated the color scheme of our brand (see attachment) and/or our main website: https://qv-lmt.org/
• - Would be nice to have some AED imagery - I attached some common symbols seen in AED advertising for inspiration
Should not have
• - This is a serious topic, so the design should be respectful and not too silly/cartoonish
• - Stock images, if chosen, should be thoughtful and classy

```html
<!DOCTYPE html>
<html lang="en">
<head>
<meta charset="utf-8">
<title>Bringing AEDs in New York Online – Birchfield Vale Chapter</title>
<link rel="stylesheet" href="https://fonts.googleapis.com/css2?family=Roboto:wght@300;400;500&family=Open+Sans:wght@400;600&display=swap">
<style>
:root{
  --navy:#0c2252;
  --navy-dark:#091a40;
  --ink:#222;
  --text:#555;
  --panel:#efefef;
  --section-grey:#f0f0f0;
  --faq-grey:#777;
  --footer:#1e1e1e;
  --footer-line:#3a3a3a;
  --white:#fff;
}
*{box-sizing:border-box;margin:0;padding:0}
html,body{width:1200px;height:3364px;overflow:hidden}
body{font-family:"Open Sans",Arial,sans-serif;color:var(--text);background:var(--white);position:relative}
.container{position:absolute;left:144px;width:912px}
h2.section-title{font-family:"Roboto",Arial,sans-serif;font-weight:400;color:var(--navy);font-size:32px;text-align:center;width:100%}
.btn{display:inline-block;background:var(--navy);color:var(--white);font-family:"Roboto",Arial,sans-serif;font-size:13px;border-radius:2px;text-align:center}

/* hero */
.hero{position:absolute;left:0;top:0;width:1200px;height:614px;background:linear-gradient(100deg,#dcdcdc 0%,#ececec 45%,#e2e2e2 100%)}
.hero-visual{position:absolute;left:690px;top:95px;width:230px;height:430px;background:linear-gradient(180deg,#f4f4f4,#d8d8d8);border-radius:4px;opacity:.85}
.brand{position:absolute;left:144px;top:16px;display:flex;align-items:center;gap:12px}
.brand-mark{width:60px;height:60px;border-radius:50%;background:var(--navy)}
.brand-name{font-family:"Open Sans",Arial,sans-serif;color:var(--navy);font-size:20px;font-weight:400;line-height:1.1}
.nav{position:absolute;top:30px;right:144px;display:flex;gap:38px;font-family:"Roboto",Arial,sans-serif;font-size:12px;color:var(--ink)}
.nav .active{color:var(--navy);border-bottom:1px solid var(--navy);padding-bottom:3px}
.hero-title{position:absolute;left:142px;top:268px;font-family:"Roboto",Arial,sans-serif;font-weight:400;font-size:48px;line-height:56px;color:var(--navy)}
.hero .btn{position:absolute;left:144px;top:385px;width:96px;height:39px;line-height:39px}
.arrow{position:absolute}

/* welcome */
.welcome-photo{position:absolute;left:144px;top:694px;width:322px;height:232px;background:linear-gradient(135deg,#6f5c44,#c86a30 35%,#d9c8b0 60%,#8aa0b0);box-shadow:8px 8px 0 var(--navy)}
.welcome-text{position:absolute;left:512px;top:686px;width:544px}
.welcome-text h2{font-family:"Roboto",Arial,sans-serif;font-weight:400;color:var(--navy);font-size:32px;margin-bottom:10px}
.welcome-text p{font-size:13px;line-height:24px;color:#666}
.welcome-text .btn{margin-top:14px;width:96px;height:39px;line-height:39px}

/* map */
.map{position:absolute;left:0;top:1015px;width:1200px;height:543px;background:linear-gradient(90deg,#e9ecea,#dfe5e3 50%,#e9ecea)}

/* how */
.how{top:1640px}
.steps{position:absolute;top:55px;left:0;width:912px;display:flex;gap:6px}
.step{width:300px;height:192px;background:var(--panel);text-align:center;padding-top:24px}
.step h3{font-family:"Roboto",Arial,sans-serif;font-weight:400;color:var(--navy);font-size:15px;margin-top:14px}
.step p{font-size:10.5px;color:#555;margin-top:8px}

/* faq */
.faq-band{position:absolute;left:0;top:1966px;width:1200px;height:568px;background:var(--section-grey)}
.faq{top:2043px}
.faq-list{position:absolute;top:52px;width:912px}
.faq-item{margin-bottom:8px}
.faq-q{height:40px;background:var(--faq-grey);color:var(--white);font-family:"Roboto",Arial,sans-serif;font-size:14px;display:flex;align-items:center;padding:0 16px;gap:10px;border-radius:2px}
.faq-item.open .faq-q{background:var(--navy);height:34px;border-radius:2px 2px 0 0}
.faq-q .caret{margin-left:auto}
.faq-a{background:var(--white);border:1px solid #ccc;border-top:none;padding:12px 16px 14px 42px;font-size:10px;line-height:16px;color:#555;position:relative}
.faq-a svg{position:absolute;left:15px;top:13px}
.faq .btn{position:absolute;top:367px;left:408px;width:96px;height:40px;line-height:40px}

/* blog */
.blog{top:2604px}
.posts{position:absolute;top:56px;display:flex;gap:9px}
.post{width:298px;background:var(--panel)}
.post-photo{height:200px;position:relative}
.post-date{position:absolute;left:0;bottom:0;background:var(--navy);color:var(--white);font-family:"Roboto",Arial,sans-serif;font-size:11px;padding:5px 12px}
.post p{font-family:"Roboto",Arial,sans-serif;font-size:15px;line-height:22px;color:var(--navy);padding:14px 20px 16px}

/* footer */
.footer{position:absolute;left:0;top:3036px;width:1200px;height:328px;background:var(--footer);color:#bbb}
.signup{position:absolute;left:142px;top:53px;display:flex;align-items:center;gap:11px}
.signup h2{font-family:"Roboto",Arial,sans-serif;font-weight:400;font-size:29px;color:var(--white);margin-right:1px}
.field{width:218px;height:40px;background:var(--white);border-radius:2px;color:#555;font-size:13px;padding:0 14px;line-height:40px}
.subscribe{width:136px;height:40px;line-height:40px;background:#0d2a6c;color:var(--white);font-family:"Roboto",Arial,sans-serif;font-size:14px;text-align:center;border-radius:2px;margin-left:1px}
.rule{position:absolute;left:144px;top:136px;width:912px;height:1px;background:var(--footer-line)}
.foot-links{position:absolute;left:144px;top:166px;font-size:10px;color:#aaa}
.foot-links span{margin:0 7px}
.copyright{position:absolute;left:144px;top:192px;font-size:10px;color:#aaa}
.socials{position:absolute;left:143px;top:245px;display:flex;gap:15px}
.social{width:41px;height:41px;border:1px solid #888;border-radius:50%}
.contact{position:absolute;left:814px;top:164px;font-size:15px;color:#ccc;font-family:"Roboto",Arial,sans-serif}
.contact div{display:flex;align-items:center;gap:9px;margin-bottom:12px}
.contact .mail{font-size:12px;font-family:"Open Sans",Arial,sans-serif}
.chat{position:absolute;left:816px;top:226px;width:240px;height:56px;background:#2f2f2f;display:flex;align-items:center;gap:14px;padding-left:16px}
.chat small{display:block;font-size:10px;color:#bbb}
.chat strong{display:block;font-family:"Roboto",Arial,sans-serif;font-weight:400;font-size:18px;color:#ddd}
</style>
</head>
<body>

<header class="hero">
  <div class="hero-visual" role="img" aria-label="Wall-mounted AED sign above a white defibrillator cabinet in a bright hallway"></div>
  <div class="brand">
    <span class="brand-mark"></span>
    <span class="brand-name">Birchfield Vale<br>Chapter</span>
  </div>
  <nav class="nav">
    <span class="active">HOME</span><span>AED</span><span>HOW IT WORKS</span><span>FAQ</span><span>ABOUT US</span><span>CONTACT US</span>
  </nav>
  <svg class="arrow" style="left:54px;top:332px" width="16" height="28" viewBox="0 0 16 28"><path d="M14 2 3 14l11 12" fill="none" stroke="#0c2252" stroke-width="3"/></svg>
  <svg class="arrow" style="left:1127px;top:332px" width="16" height="28" viewBox="0 0 16 28"><path d="M2 2l11 12L2 26" fill="none" stroke="#0c2252" stroke-width="3"/></svg>
  <h1 class="hero-title">Bringing AEDs in<br>New York Online</h1>
  <span class="btn">Read More</span>
</header>

<section>
  <div class="welcome-photo" role="img" aria-label="Hands placing AED pads on a training manikin beside an orange defibrillator"></div>
  <div class="welcome-text">
    <h2>Welcome</h2>
    <p>Etiam quis aliquet risus. Duis ornare erat eget magna dapibus, in accumsan quam pharetra. Nam tempus, quam in bibendum vulputate, sapien dolor viverra nisl, vitae euismod elit turpis et nulla. Aliquam erat volutpat. Pellentesque blandit lacus eget nunc faucibus, et tincidunt eros viverra. Phasellus consequat sagittis nisi suscipit feugiat. Cras eget leo sed nunc hendrerit ultricies eu at nisl. Praesent iaculis faucibus urna sit amet lacinia. Maecenas consequat justo enim, ac mattis massa imperdiet quis.</p>
    <span class="btn">Read More</span>
  </div>
</section>

<section class="map" role="img" aria-label="Muted grey street map of the New York City region with pins marking participating regions"></section>

<section class="container how">
  <h2 class="section-title">How It Works</h2>
  <div class="steps">
    <div class="step">
      <svg width="84" height="76" viewBox="0 0 84 76" fill="none" stroke="#333" stroke-width="2"><path d="M42 62S20 38 20 24a22 22 0 0 1 44 0c0 14-22 38-22 38z"/><circle cx="42" cy="24" r="9"/><path d="M26 54H12L4 72h76l-8-18H58"/></svg>
      <h3>ALIQUAM ERAT</h3>
      <p>Etiam mattis augue vehicula odio posuere sit amet</p>
    </div>
    <div class="step">
      <svg width="84" height="76" viewBox="0 0 84 76" fill="none" stroke="#333" stroke-width="2"><rect x="4" y="2" width="76" height="40" rx="3"/><rect x="10" y="8" width="50" height="26"/><path d="M12 22h14l4-8 4 14 4-6h18"/><circle cx="70" cy="14" r="3"/><circle cx="70" cy="26" r="3"/><path d="M14 42v30M32 42v18h-8v12M52 42v18h8v12M70 42v30"/></svg>
      <h3>FUSCE VITAE</h3>
      <p>Quisque aliquet ex nec est vestibulum pulvinar</p>
    </div>
    <div class="step">
      <svg width="84" height="76" viewBox="0 0 84 76" fill="none" stroke="#333" stroke-width="2"><path d="M4 4h52v32H24l-10 8v-8H4z"/><path d="M26 14a4 4 0 1 1 4 5v4M30 28v2"/><path d="M40 42h40v28h-8v6l-8-6H40z"/><circle cx="60" cy="54" r="6"/><path d="M57 60v4h6v-4"/></svg>
      <h3>VESTIBULUM ANTE</h3>
      <p>Pellentesque convallis molestie enim sit amet</p>
    </div>
  </div>
</section>

<div class="faq-band"></div>
<section class="container faq">
  <h2 class="section-title">FAQs</h2>
  <div class="faq-list">
    <div class="faq-item open">
      <div class="faq-q"><svg width="14" height="14" viewBox="0 0 14 14"><circle cx="7" cy="7" r="7" fill="#fff"/><text x="7" y="11" font-size="10" text-anchor="middle" fill="#0c2252" font-family="Arial" font-weight="700">?</text></svg>Phasellus condimentum vitae faucibus sollicitudin metus?<svg class="caret" width="10" height="6" viewBox="0 0 10 6"><path d="M0 6 5 0l5 6z" fill="#fff"/></svg></div>
      <div class="faq-a"><svg width="13" height="13" viewBox="0 0 14 14"><circle cx="7" cy="7" r="7" fill="#666"/><rect x="6" y="6" width="2" height="5" fill="#fff"/><rect x="6" y="3" width="2" height="2" fill="#fff"/></svg>Aliquam erat volutpat. Quisque aliquet ex nec est vestibulum pulvinar. Pellentesque convallis molestie enim sit amet efficitur. Etiam id imperdiet lectus. Vivamus lacus justo, ultrices nec erat in, euismod iaculis mauris. Vivamus eleifend vitae nulla vel malesuada. In ac malesuada lacus, et consectetur ante. Fusce vitae lectus sit amet mi pulvinar maximus. Aenean placerat, nibh vel accumsan aliquet, magna nibh accumsan nibh.</div>
    </div>
    <div class="faq-item"><div class="faq-q"><svg width="14" height="14" viewBox="0 0 14 14"><circle cx="7" cy="7" r="7" fill="#fff"/><text x="7" y="11" font-size="10" text-anchor="middle" fill="#777" font-family="Arial" font-weight="700">?</text></svg>Nullam accumsan purus vel tempus viverra?<svg class="caret" width="10" height="6" viewBox="0 0 10 6"><path d="M0 0h10L5 6z" fill="#fff"/></svg></div></div>
    <div class="faq-item"><div class="faq-q"><svg width="14" height="14" viewBox="0 0 14 14"><circle cx="7" cy="7" r="7" fill="#fff"/><text x="7" y="11" font-size="10" text-anchor="middle" fill="#777" font-family="Arial" font-weight="700">?</text></svg>Donec sit amet lectus nec mi tempor laoreet ac nec?<svg class="caret" width="10" height="6" viewBox="0 0 10 6"><path d="M0 0h10L5 6z" fill="#fff"/></svg></div></div>
    <div class="faq-item"><div class="faq-q"><svg width="14" height="14" viewBox="0 0 14 14"><circle cx="7" cy="7" r="7" fill="#fff"/><text x="7" y="11" font-size="10" text-anchor="middle" fill="#777" font-family="Arial" font-weight="700">?</text></svg>Mauris suscipit felis id nunc elementum varius?<svg class="caret" width="10" height="6" viewBox="0 0 10 6"><path d="M0 0h10L5 6z" fill="#fff"/></svg></div></div>
    <div class="faq-item"><div class="faq-q"><svg width="14" height="14" viewBox="0 0 14 14"><circle cx="7" cy="7" r="7" fill="#fff"/><text x="7" y="11" font-size="10" text-anchor="middle" fill="#777" font-family="Arial" font-weight="700">?</text></svg>Nullam accumsan purus vel tempus?<svg class="caret" width="10" height="6" viewBox="0 0 10 6"><path d="M0 0h10L5 6z" fill="#fff"/></svg></div></div>
  </div>
  <span class="btn">View All</span>
</section>

<section class="container blog">
  <h2 class="section-title">Blog</h2>
  <svg class="arrow" style="left:-90px;top:165px" width="16" height="28" viewBox="0 0 16 28"><path d="M14 2 3 14l11 12" fill="none" stroke="#666" stroke-width="3"/></svg>
  <svg class="arrow" style="left:983px;top:165px" width="16" height="28" viewBox="0 0 16 28"><path d="M2 2l11 12L2 26" fill="none" stroke="#666" stroke-width="3"/></svg>
  <div class="posts">
    <article class="post">
      <div class="post-photo" role="img" aria-label="Navy automatic external defibrillator sign on a wall" style="background:linear-gradient(120deg,#d8d2bf 0%,#c8c0a8 30%,#1b2a7a 45%,#16236a 100%)"><span class="post-date">10 June, 2019</span></div>
      <p>Proin porta fermentum porttitor turpis venenatis luctus feugiat viver ra lorem ac sagittis.</p>
    </article>
    <article class="post">
      <div class="post-photo" role="img" aria-label="Person on a phone call standing beside a public AED cabinet" style="background:linear-gradient(100deg,#5a5a5a 0%,#e9d8d0 40%,#b9c2bd 70%,#8d968f 100%)"><span class="post-date">10 June, 2019</span></div>
      <p>Nullam accumsan purus vel tempus viverra. Mauris suscipit felis id nunc elementum varius.</p>
    </article>
    <article class="post">
      <div class="post-photo" role="img" aria-label="Wall-mounted AED cabinet in an office corridor" style="background:linear-gradient(100deg,#cfd3d4 0%,#eeeeee 45%,#b7bcbc 80%,#6e7577 100%)"><span class="post-date">10 June, 2019</span></div>
      <p>Praesent elementum nulla sit amet justo pellentesque scelerisque. Nam et tortor ante iaculis porttitor.</p>
    </article>
  </div>
</section>

<footer class="footer">
  <div class="signup">
    <h2>NEWSLETTER SIGNUP</h2>
    <div class="field">Name</div>
    <div class="field">Email</div>
    <div class="subscribe">SUBSCRIBE</div>
  </div>
  <div class="rule"></div>
  <div class="foot-links">Home<span>|</span>AED<span>|</span>How It Works<span>|</span>FAQ<span>|</span>About Us<span>|</span>Contact Us</div>
  <div class="copyright">Copyright © 2019 &nbsp;AED. &nbsp;All rights reserved.</div>
  <div class="socials">
    <span class="social" aria-label="Social profile"></span>
    <span class="social" aria-label="Social profile"></span>
    <span class="social" aria-label="Social profile"></span>
    <span class="social" aria-label="Social profile"></span>
  </div>
  <div class="contact">
    <div><svg width="13" height="13" viewBox="0 0 24 24"><path d="M6.6 10.8a15 15 0 0 0 6.6 6.6l2.2-2.2a1 1 0 0 1 1-.25 11 11 0 0 0 3.6.6 1 1 0 0 1 1 1V20a1 1 0 0 1-1 1A17 17 0 0 1 3 4a1 1 0 0 1 1-1h3.5a1 1 0 0 1 1 1 11 11 0 0 0 .6 3.6 1 1 0 0 1-.25 1z" fill="#bbb"/></svg>555 014 2290</div>
    <div class="mail"><svg width="13" height="10" viewBox="0 0 13 10"><rect width="13" height="10" rx="1" fill="#bbb"/><path d="M0 1l6.5 5L13 1" fill="none" stroke="#1e1e1e" stroke-width="1.2"/></svg>hello@birchfieldvale.org</div>
  </div>
  <div class="chat">
    <svg width="42" height="32" viewBox="0 0 42 32"><ellipse cx="17" cy="13" rx="16" ry="12" fill="#ccc"/><path d="M8 22l-3 8 9-5z" fill="#ccc"/><ellipse cx="29" cy="19" rx="12" ry="9" fill="#999"/></svg>
    <div><small>Need online help?</small><strong>Let's chat with us</strong></div>
  </div>
</footer>

</body>
</html>
```